Mobile Repair Service on location needs a Web Design

We are starting a new mobile device repair service called Handset Haven and our website needs a design!

Hello Designers!
First, we'd like to make clear this is more than a simple web design contest, we want the designers to create an idea. We want someone who can create the whole theme of the service's we provide. We want someone that can help design our visual branding, help us communicate a sentiment. And we are willing to pay for that.

Who are we?
Our company is based in Rotterdam, the Netherlands. We provide different services for all kinds of electronic devices. The kind of services we provide are, among other things, installations of hardware and software and the repair of broken or malfunctioning devices.
We are starting a new service that offers mobile device repairs on location, be it at the home of our customers, their office, or any other place. Just give us the address and we will come to you for the repair job. This is also our main USP. We have multiple skilled engineers who drive trough the country on a daily basis and can be on location within a working day. Repair is done immediately onsite while the customer waits. At this stage we will start with the smartphone product-group within the mobile devices. In a second phase we might also add tablets.
People don't want to be without their phone for weeks because of some parts that needed to be ordered by a repair center they had to sent their phone to. We offer a fully functional mobile repair center in the form of specially customized vans. These vans have all the tools and utilities needed by our engineers to safely repair your mobile device. Your phone is being repaired directly in front of you, the next business-day, on a location you desire.

For this new service we are creating a website called Handset Haven. The website needs a story and matching design and this is where you come in. We are not looking for a simple template design we can get from any place. We need a story. We want you to create an idea, build a unique theme or vision that helps sell the product/service. This goes beyond the design of the website. We need the whole package, the design you are creating needs to have returning elements like icons, color use, images, maybe even characters etc. You name it! There needs to be a common thread in the design so we can reuse elements in, for example, the email templates, the work order or receipt we give to our customers (we may contact the winner of the contest to design these for us as well!).

The name 'Handset Haven' is chosen. Rehab (short for rehabilitate) has a bold and playful tone to it and the design needs to reflect the name. So we're looking for a somewhat playful and cheeky design. Definitely not too serious and definitely modern. We already got a logo that we love and that fit's this description (see attached design documents for the logo). It's bold, powerful and fun. Our web design needs to reflect this as well and has to fit in with our logo.
We would really like it if the design somehow incorporates elements that highlight our unique selling points (repairs on location, we come to you etc.). We would really like some form of story telling in the design. Think clumsy people breaking their phones. Teenagers in tears because they have no access to their friends. People nowadays have the need to always be 'connected'. What happens when your phone is broken or malfunctioning? We're handling tech, we are nerds and a little bit weird, but we're professionals and here to help you with your problem. The sentiment Byte Brigade tries to communicate is something we really like. We're looking for fresh idea's, anything goes!

In an overview all Unique Selling Points of the Handset haven service:
- Professional service on location. Don’t ship to us we will come to you!
- Clear pricing upfront. No hidden cost.
- Next business-day repair.
- Backed by a professional call center open 12 hours a day and open on a Saturday as well
- Backed by a professional repair center with more then 12 years of experience
- Repair is done by certified engineers
- 1 year warranty on the repair

The process:
The main function of our website will be for customers to make a repair request. A customer will visit our website and can make a repair request immediately by going through a 'request-order-flow'. In this flow he or she will need to fill in some forms and can select wich type/model/brand of mobile device he or she has and what parts need to be repaired. After a request is placed we will call the customer back (within an hour) for a short intake and to set a date/time and location. Our engineer will meet the customer at the specified location and will repair the device onsite in one of our mobile repair centers, which is a specialized van equipped with all the tools needed for device restorations.
So in short the steps are:
- Choose your device and repair job
- Place the order
- Get a callback within the hour
- Set date and location
- We will come to you.

Website functionality:
Our website is our main form of communication. So the sentiment we want to communicate needs be reflected in the design. We need a main/front page designed (preferably a long scrolling page design) containing:
1. Customers will be able to request a repair job directly on our website. So there will need to be a prominent button/link at the top of our main page that will bring the customer to this 'request-order-flow'. This is the main flow which needs to be full focus on the front page. All other items are secondary.
2. The general information of who we are and what we do, and why the customer should choose us. Preferably in short bullet-point type keywords/sentences with icons or other visual cues. See our unique selling points to get an idea of the information that will be displayed here.
3. There needs to be a section that will explain the process (see above) of a repair request step-by- step, again in brief short key sentences and with (custom) icons.
4. There needs to be a section that explains to the customer he/she can always contact us if they are not sure what the problem is with their device, and for this reason are not sure what repair request they should order.
5. We want to implement some functionality that display customer ratings or customer reviews. So there needs to be room for some kind of widget of plugin we're going to implement which shows these reviews.
6. A 'For business section' where we will explain all the options we provide for corporate clients.
7. Social media links.
8. There needs to be a menu with buttons that leads to the all sections described in the previous points.

For now, we need a design for our front page. In the second phase, when we have picked our winner, we may ask the winner to design the page(s) for our request workflow as well.

EDIT:
Finally, we have a very specific order in mind for the different segments of our website. We would like you to add some more segments that were not in our original brief as well:

1. Top header with order/request button. (should instantly make clear our main USP, we do repairs on location)
2. Our process
3. Our unique selling points / why choose us
4. The kind of repairs we do (broken screens, broken batteries, water damage, broken camera's, no sound etc.)
5. A 'meet our team' section, where we introduce some of our engineers
6. A 'contact us for any questions' section/
7. Testimonials/user reviews
8. A section where we show key performance indicators
9. 'For businesses' sections
10.'Subscribe for newsletter' field
11. Social media buttons

Industry/Entity Type

It Service

Number of Pages Required

1 page

Font styles to use
Sans Serif

Requirements
Must have
• a main/front page, design only
• custom icons/images for banners, adverts online and in print (high res)
Nice to have
• Storytelling in our design.
• Design that fits with our brand new logo.
• Elements like icons to have a flat design.
• Keep in mind that the website will need to be responsive when designing! (Ideally provide an example of the mobile design as well)
• Create a fun and trustworthy feeling.

```html
<!DOCTYPE html>
<html lang="en">
<head>
<meta charset="utf-8">
<title>Handset Haven – Mobile Repair On Location</title>
<link href="https://fonts.googleapis.com/css2?family=Lato:wght@400;700;900&display=swap" rel="stylesheet">
<style>
:root{
  --orange:#ee5a24;
  --orange-dark:#d94c18;
  --ink:#333333;
  --text:#555555;
  --muted:#888888;
  --nav:#4b4b4b;
  --pin:#555555;
  --tint:#f2ebe8;
  --dark:#2b2b2b;
  --darker:#222222;
  --footer:#333333;
  --white:#ffffff;
  --line:#dddddd;
}
*{box-sizing:border-box;margin:0;padding:0}
html,body{width:1200px;height:3186px;overflow:hidden}
body{font-family:'Lato',sans-serif;color:var(--text);background:var(--white);position:relative}
a{color:inherit;text-decoration:none}
.wrap{width:1030px;margin:0 auto;position:relative}

/* header */
.site-header{height:142px;background:var(--white)}
.site-header .wrap{height:142px}
.brand{position:absolute;left:0;top:26px;display:flex;align-items:center;gap:14px}
.brand-mark{width:62px;height:62px;border-radius:50%;background:var(--orange)}
.brand-name{font-weight:900;font-size:34px;line-height:32px;color:var(--ink);text-transform:uppercase}
.brand-tag{font-size:13px;color:var(--muted);margin-top:4px}
.util-links{position:absolute;right:0;top:20px;font-size:13px;color:var(--ink);font-weight:700;display:flex;gap:14px}
.util-links span+span::before{content:"|";margin-right:14px;color:var(--muted);font-weight:400}
.call{position:absolute;left:455px;top:66px;display:flex;align-items:center;gap:12px}
.call-icon{width:40px;height:40px;border:2px solid var(--orange);border-radius:50%;display:flex;align-items:center;justify-content:center}
.call-label{font-size:13px;font-weight:700;color:var(--ink)}
.call-number{font-size:19px;color:var(--ink)}
.search{position:absolute;right:0;top:70px;display:flex}
.search-field{width:280px;height:40px;border:1px solid var(--line);font-size:12px;color:#aaa;padding:12px 16px}
.search-btn{width:42px;height:40px;background:var(--orange);display:flex;align-items:center;justify-content:center}

.main-nav{height:64px;background:var(--nav)}
.main-nav ul{list-style:none;display:flex;justify-content:space-between;height:64px;align-items:center;font-size:16px;font-weight:700;color:var(--white)}
.main-nav li{display:flex;align-items:center}
.main-nav li+li::before{content:"|";margin-right:24px;font-weight:400;color:#bbb}
.main-nav .current{color:var(--orange)}

/* hero */
.hero{height:357px;position:relative;background:linear-gradient(100deg,#151515 0%,#2c2a28 40%,#4a3a30 65%,#2a2421 100%);color:var(--white)}
.hero-title{position:absolute;left:85px;top:98px;font-size:42px;font-weight:900;text-transform:uppercase}
.hero-text{position:absolute;left:85px;top:160px;width:650px;font-size:17px;line-height:26px}
.btn-orange{display:inline-block;background:var(--orange);color:var(--white);text-transform:uppercase;font-size:17px;padding:14px 24px}
.hero .btn-orange{position:absolute;left:85px;top:225px}
.hero-arrow{position:absolute;top:160px}

/* process */
.process{height:463px;text-align:center}
.section-title{font-size:21px;font-weight:900;color:var(--ink);text-transform:uppercase}
.section-title em{font-style:normal;color:var(--orange)}
.process .section-title{padding-top:70px}
.steps{position:relative;display:flex;justify-content:space-between;margin-top:34px}
.steps::before{content:"";position:absolute;left:80px;right:80px;top:62px;border-top:3px dotted #666}
.step{width:160px;position:relative}
.step svg{display:block;margin:0 auto}
.step-label{margin-top:22px;font-size:13px;font-weight:900;text-transform:uppercase;color:var(--ink);line-height:19px}
.step.active .step-label{color:var(--orange)}

/* categories */
.categories{height:539px;background:var(--tint);text-align:center}
.categories .section-title{padding-top:66px}
.cat-list{display:flex;justify-content:space-between;margin-top:40px;padding:0 20px}
.cat{width:216px}
.cat-ring{width:210px;height:210px;border-radius:50%;border:6px solid #e3dcd8;background:#d6d3d1;display:flex;align-items:center;justify-content:center;margin:0 auto}
.cat.active .cat-ring{background:var(--orange);border-color:var(--white);box-shadow:0 0 0 3px var(--orange)}
.cat-name{margin-top:24px;font-size:17px;text-transform:uppercase;color:var(--ink)}
.cat.active .cat-name{color:var(--orange)}
.dots{display:flex;justify-content:center;gap:12px;margin-top:40px}
.dots span{width:22px;height:22px;border-radius:50%;border:2px solid #444}
.dots .on{border-color:var(--orange);background:radial-gradient(var(--orange) 50%,transparent 55%)}

/* about */
.about{height:453px}
.about-text{position:absolute;left:0;top:64px;width:630px}
.about h2{font-size:21px;font-weight:900;text-transform:uppercase;color:var(--ink);margin-bottom:14px}
.about p{font-size:11.5px;line-height:19px;text-align:justify;margin-bottom:14px}
.btn-dark{display:inline-block;background:#111;color:var(--white);font-size:14px;font-weight:700;padding:15px 26px;margin-top:12px}
.about-photo{position:absolute;right:2px;top:64px;width:389px;height:321px;background:linear-gradient(135deg,#e6e6e6,#bfbfbf 60%,#8e8e8e)}

/* quote */
.quote{height:637px;position:relative;background:linear-gradient(120deg,#1b1b1b 0%,#2e2a27 45%,#4a3b31 75%,#1e1e1e 100%);color:var(--white)}
.quote-title{position:absolute;left:85px;top:40px;font-size:21px;font-weight:900;text-transform:uppercase}
.usp-list{position:absolute;left:85px;top:110px;width:540px;list-style:none}
.usp-list li{display:flex;align-items:center;gap:18px;min-height:68px;font-size:13px;line-height:19px}
.usp-icon{flex:none;width:38px;height:38px;border-radius:50%;background:var(--orange);display:flex;align-items:center;justify-content:center}
.swoosh{position:absolute;left:320px;top:20px}
.quote-card{position:absolute;left:631px;top:-21px;width:482px;height:616px;background:var(--white);box-shadow:0 4px 20px rgba(0,0,0,.35);color:var(--text)}
.quote-card-head{background:var(--orange);color:var(--white);font-size:16px;line-height:24px;text-align:center;padding:13px 30px;height:74px}
.quote-form{padding:34px 34px 0}
.select{height:48px;border:1px solid var(--line);margin-bottom:10px;font-size:12px;color:var(--ink);display:flex;align-items:center;justify-content:space-between;padding:0 18px}
.select::after{content:"";border:5px solid transparent;border-top-color:#333;margin-top:5px}
.fix-label{font-size:13px;color:var(--ink);margin:10px 0 12px}
.option{font-size:12px;color:var(--ink);display:flex;align-items:center;gap:12px;margin:0 0 8px 14px}
.option::before{content:"";width:11px;height:11px;border:1.5px solid #333;border-radius:50%}
.quote-card .btn-orange{display:block;width:222px;margin:34px auto 0;text-align:center;font-size:16px;padding:15px 0}

/* follow + newsletter */
.connect{height:212px;background:var(--dark);color:var(--white)}
.follow{position:absolute;left:0;top:44px;width:530px;text-align:center}
.connect h3{font-size:21px;font-weight:700;text-transform:uppercase}
.social{display:flex;justify-content:center;gap:6px;margin-top:20px}
.social span{width:38px;height:38px;background:var(--orange)}
.newsletter{position:absolute;left:500px;top:44px;width:530px;text-align:center}
.newsletter p{font-size:12px;margin-top:8px}
.news-form{display:flex;justify-content:center;margin-top:14px}
.news-field{width:284px;height:46px;background:var(--white);color:#999;font-size:12px;padding:16px 22px;text-align:left}
.news-btn{width:56px;height:46px;background:var(--orange);display:flex;align-items:center;justify-content:center}

/* footer */
.site-footer{height:266px;background:var(--footer);color:#ddd;border-top:1px solid #444}
.foot-col{position:absolute;top:52px}
.foot-col h4{font-size:17px;font-weight:400;color:var(--white);text-transform:uppercase;margin-bottom:20px}
.foot-col ul{list-style:none;font-size:12px;line-height:25px}
.contact-list li{display:flex;gap:18px;align-items:flex-start;line-height:22px;margin-bottom:2px}
.contact-list svg{flex:none;margin-top:5px}
.bottom-bar{height:53px;background:var(--darker);color:#ddd;font-size:12px}
.bottom-bar .wrap{padding-top:20px;padding-left:18px}
</style>
</head>
<body>

<header class="site-header">
  <div class="wrap">
    <div class="brand">
      <span class="brand-mark"></span>
      <div>
        <div class="brand-name">Handset<br>Haven</div>
        <div class="brand-tag">We will come to you!</div>
      </div>
    </div>
    <div class="util-links"><span>WISH LISTS</span><span>LOG IN</span><span>REGISTER</span><span>CART</span></div>
    <div class="call">
      <span class="call-icon"><svg width="18" height="18" viewBox="0 0 24 24"><path d="M6.6 10.8a15 15 0 0 0 6.6 6.6l2.2-2.2a1 1 0 0 1 1-.25 11.4 11.4 0 0 0 3.6.57 1 1 0 0 1 1 1V20a1 1 0 0 1-1 1A17 17 0 0 1 3 4a1 1 0 0 1 1-1h3.5a1 1 0 0 1 1 1c0 1.25.2 2.45.57 3.57a1 1 0 0 1-.25 1z" fill="#333"/></svg></span>
      <div><div class="call-label">CALL TO</div><div class="call-number">18 000 555 010</div></div>
    </div>
    <div class="search">
      <div class="search-field">Search</div>
      <div class="search-btn"><svg width="16" height="16" viewBox="0 0 24 24"><circle cx="10" cy="10" r="6.5" fill="none" stroke="#fff" stroke-width="2.5"/><path d="M15 15l6 6" stroke="#fff" stroke-width="2.5"/></svg></div>
    </div>
  </div>
</header>

<nav class="main-nav">
  <ul class="wrap">
    <li class="current">HOME</li><li>PHONE REPAIRS</li><li>ABOUT US</li><li>SUPPORT</li><li>WHAT WE DO</li><li>HOW IT WORK</li><li>BLOG</li><li>CONTACT US</li>
  </ul>
</nav>

<section class="hero" role="img" aria-label="Photo of hands repairing an opened smartphone with small tools">
  <svg class="hero-arrow" style="left:28px" width="22" height="40" viewBox="0 0 22 40"><path d="M18 2L4 20l14 18" fill="none" stroke="#fff" stroke-width="2"/></svg>
  <svg class="hero-arrow" style="right:28px" width="22" height="40" viewBox="0 0 22 40"><path d="M4 2l14 18L4 38" fill="none" stroke="#fff" stroke-width="2"/></svg>
  <h1 class="hero-title">Welcome to Handset Haven</h1>
  <p class="hero-text">The main function of our website will be for customers to make a repair request. A customer will visit our website and can make a repair request immediately</p>
  <a class="btn-orange">Request Order Flow</a>
</section>

<section class="process">
  <div class="wrap">
    <h2 class="section-title">How it works at <em>Handset Haven</em></h2>
    <div class="steps">
      <div class="step">
        <svg width="128" height="178" viewBox="0 0 128 178"><path d="M64 2C30 2 4 28 4 62c0 44 60 114 60 114s60-70 60-114C124 28 98 2 64 2z" fill="#555"/><circle cx="64" cy="62" r="34" fill="#fff"/><rect x="52" y="42" width="24" height="40" rx="4" fill="none" stroke="#555" stroke-width="3"/><circle cx="64" cy="75" r="2.5" fill="#555"/></svg>
        <div class="step-label">Choose your device<br>and repair job</div>
      </div>
      <div class="step">
        <svg width="128" height="178" viewBox="0 0 128 178"><path d="M64 2C30 2 4 28 4 62c0 44 60 114 60 114s60-70 60-114C124 28 98 2 64 2z" fill="#555"/><circle cx="64" cy="62" r="34" fill="#fff"/><path d="M44 64l20-20 20 20h-6v18H50V64z" fill="#555"/></svg>
        <div class="step-label">Place the order</div>
      </div>
      <div class="step active">
        <svg width="128" height="178" viewBox="0 0 128 178"><path d="M64 2C30 2 4 28 4 62c0 44 60 114 60 114s60-70 60-114C124 28 98 2 64 2z" fill="#ee5a24" stroke="#fff" stroke-width="3"/><circle cx="64" cy="62" r="34" fill="#fff"/><path d="M53 48l6 6-4 5a20 20 0 0 0 10 10l5-4 6 6-4 5c-14 0-24-10-24-24z" fill="#ee5a24"/><path d="M68 46a12 12 0 0 1 10 10M68 52a6 6 0 0 1 4 4" fill="none" stroke="#ee5a24" stroke-width="2.5"/></svg>
        <div class="step-label">Get a callback<br>within the hour</div>
      </div>
      <div class="step">
        <svg width="128" height="178" viewBox="0 0 128 178"><path d="M64 2C30 2 4 28 4 62c0 44 60 114 60 114s60-70 60-114C124 28 98 2 64 2z" fill="#555"/><circle cx="64" cy="62" r="34" fill="#fff"/><rect x="46" y="46" width="30" height="30" rx="2" fill="none" stroke="#555" stroke-width="3"/><path d="M46 54h30M53 42v8M69 42v8" stroke="#555" stroke-width="3"/><circle cx="77" cy="74" r="9" fill="#fff" stroke="#555" stroke-width="3"/><path d="M77 69v5h4" stroke="#555" stroke-width="2" fill="none"/></svg>
        <div class="step-label">Set date and<br>location</div>
      </div>
      <div class="step">
        <svg width="128" height="178" viewBox="0 0 128 178"><path d="M64 2C30 2 4 28 4 62c0 44 60 114 60 114s60-70 60-114C124 28 98 2 64 2z" fill="#555"/><circle cx="64" cy="62" r="34" fill="#fff"/><path d="M42 52h28v20H42zM70 58h10l6 7v7H70z" fill="#555"/><circle cx="50" cy="74" r="4" fill="#555" stroke="#fff" stroke-width="2"/><circle cx="78" cy="74" r="4" fill="#555" stroke="#fff" stroke-width="2"/></svg>
        <div class="step-label">We will<br>come to you.</div>
      </div>
    </div>
  </div>
</section>

<section class="categories">
  <div class="wrap">
    <h2 class="section-title">Choose your Handset Haven service by category</h2>
    <div class="cat-list">
      <div class="cat">
        <div class="cat-ring"><svg width="110" height="80" viewBox="0 0 110 80"><rect x="2" y="6" width="106" height="66" rx="4" fill="#3a3a3a"/><rect x="12" y="16" width="60" height="46" fill="#d6d3d1"/><rect x="82" y="16" width="18" height="10" fill="#d6d3d1"/><circle cx="91" cy="40" r="4" fill="#d6d3d1"/><circle cx="91" cy="54" r="4" fill="#d6d3d1"/></svg></div>
        <div class="cat-name">Appliances</div>
      </div>
      <div class="cat">
        <div class="cat-ring"><svg width="110" height="84" viewBox="0 0 110 84"><path d="M8 20h24l8-12h30l8 12h24v60H8z" fill="#3a3a3a"/><circle cx="55" cy="48" r="22" fill="#d6d3d1"/><circle cx="55" cy="48" r="14" fill="#3a3a3a"/></svg></div>
        <div class="cat-name">Camera &amp; Camcorder</div>
      </div>
      <div class="cat active">
        <div class="cat-ring"><svg width="120" height="80" viewBox="0 0 120 80"><path d="M50 14a14 14 0 0 1 20 0M54 19a7 7 0 0 1 12 0" fill="none" stroke="#fff" stroke-width="3"/><path d="M6 52v-10l16-4 14-14h44l16 14 16 4v10z" fill="#fff"/><path d="M40 28h16v10H30zM62 28h14l10 10H62z" fill="#ee5a24"/><circle cx="30" cy="54" r="9" fill="#fff" stroke="#ee5a24" stroke-width="3"/><circle cx="90" cy="54" r="9" fill="#fff" stroke="#ee5a24" stroke-width="3"/></svg></div>
        <div class="cat-name">Car Electronics</div>
      </div>
      <div class="cat">
        <div class="cat-ring"><svg width="60" height="110" viewBox="0 0 60 110"><rect x="3" y="3" width="54" height="104" rx="8" fill="none" stroke="#3a3a3a" stroke-width="4"/><rect x="9" y="14" width="42" height="80" fill="#fff"/><rect x="22" y="7" width="16" height="3" fill="#3a3a3a"/></svg></div>
        <div class="cat-name">Cell Phone</div>
      </div>
    </div>
    <div class="dots"><span></span><span class="on"></span><span></span></div>
  </div>
</section>

<section class="about">
  <div class="wrap">
    <div class="about-text">
      <h2>About Handset Haven</h2>
      <p>Our company is based in Rotterdam, the Netherlands. We provide different services for all kinds of electronic devices. The kind of services we provide are, among other things, installations of hardware and software and the repair of broken or malfunctioning devices. We are starting a new service that offers mobile device repairs on location, be it at the home of our customers, their office, or any other place. Just give us the address and we will come to you for the repair job. This is also our main USP. We have multiple skilled engineers who drive trough the country on a daily basis and can be on location within a working day. Repair is done immediately onsite while the customer waits. At this stage we will start with the smartphone product-group within the mobile devices. In a second phase we might also add tablets.</p>
      <p>People don't want to be without their phone for weeks because of some parts that needed to be ordered by a repair center they had to sent their phone to. We offer a fully functional</p>
      <a class="btn-dark">Read More &gt;</a>
    </div>
    <div class="about-photo" role="img" aria-label="Photo of a worried man in glasses holding a broken phone"></div>
  </div>
</section>

<section class="quote" role="img" aria-label="Dark background photo of hands working on a circuit board">
  <h2 class="quote-title">Get a quote now</h2>
  <svg class="swoosh" width="230" height="70" viewBox="0 0 230 70"><path d="M4 60C60 70 140 60 210 14" fill="none" stroke="#fff" stroke-width="2" stroke-dasharray="3 5"/><path d="M196 10l16 2-4 15" fill="none" stroke="#fff" stroke-width="2"/></svg>
  <ul class="usp-list">
    <li><span class="usp-icon"><svg width="16" height="20" viewBox="0 0 16 20"><path d="M8 1a7 7 0 0 0-7 7c0 5 7 11 7 11s7-6 7-11a7 7 0 0 0-7-7z" fill="#fff"/><circle cx="8" cy="8" r="2.5" fill="#ee5a24"/></svg></span>Professional service on location. Don't ship to us we will come to you!</li>
    <li><span class="usp-icon"><svg width="20" height="14" viewBox="0 0 20 14"><rect x="1" y="1" width="18" height="12" rx="1" fill="none" stroke="#fff" stroke-width="2"/><circle cx="10" cy="7" r="3" fill="#fff"/></svg></span>Clear pricing upfront. No hidden cost.</li>
    <li><span class="usp-icon"><svg width="18" height="18" viewBox="0 0 18 18"><rect x="1" y="3" width="16" height="14" fill="none" stroke="#fff" stroke-width="2"/><path d="M5 10l3 3 5-6" fill="none" stroke="#fff" stroke-width="2"/></svg></span>Next business-day repair.</li>
    <li><span class="usp-icon"><svg width="20" height="18" viewBox="0 0 20 18"><path d="M2 12V9a8 8 0 0 1 16 0v3" fill="none" stroke="#fff" stroke-width="2"/><rect x="1" y="10" width="5" height="7" rx="1" fill="#fff"/><rect x="14" y="10" width="5" height="7" rx="1" fill="#fff"/></svg></span>Backed by a professional call center open 12 hours a day and open on a Saturday as well</li>
    <li><span class="usp-icon"><svg width="18" height="18" viewBox="0 0 18 18"><circle cx="9" cy="9" r="5" fill="#fff"/><path d="M9 1v4M9 13v4M1 9h4M13 9h4M3.3 3.3l2.8 2.8M11.9 11.9l2.8 2.8M3.3 14.7l2.8-2.8M11.9 6.1l2.8-2.8" stroke="#fff" stroke-width="2"/></svg></span>Backed by a professional repair center with more then 12 years of experience</li>
    <li><span class="usp-icon"><svg width="16" height="18" viewBox="0 0 16 18"><path d="M8 1l7 3v5c0 4-3 7-7 8-4-1-7-4-7-8V4z" fill="#fff"/></svg></span>Repair is done by certified engineers</li>
    <li><span class="usp-icon"><svg width="18" height="18" viewBox="0 0 18 18"><path d="M9 1l2.4 5.2 5.6.6-4.2 3.8 1.2 5.6L9 13.4 4 16.2l1.2-5.6L1 6.8l5.6-.6z" fill="#fff"/></svg></span>1 year warranty on the repair</li>
  </ul>
  <div class="quote-card">
    <div class="quote-card-head">Try our quick quote to get an instant no fix, no fee repair estimate for your mobile phone!</div>
    <div class="quote-form">
      <div class="select">Please select a Manufacturer</div>
      <div class="select">Please select a Model</div>
      <div class="select">Please select a Problem</div>
      <div class="select">Please select a phone age</div>
      <div class="fix-label">Fix my device in:</div>
      <div class="option">24 Hours - Return Cost £14.95</div>
      <div class="option">2-3 Days - Return Cost £7.95</div>
      <div class="option">3-5 Days - FREE Swift Post Return</div>
      <a class="btn-orange">Get a Quote</a>
    </div>
  </div>
</section>

<section class="connect">
  <div class="wrap">
    <div class="follow">
      <h3>Follow Us</h3>
      <div class="social" aria-label="Social media links"><span></span><span></span><span></span><span></span><span></span><span></span></div>
    </div>
    <div class="newsletter">
      <h3>Newsletter Subscription</h3>
      <p>Subscribe to our newsletter for deals and coupons.</p>
      <div class="news-form">
        <div class="news-field">Your email</div>
        <div class="news-btn"><svg width="20" height="20" viewBox="0 0 20 20"><path d="M1 9L19 1l-6 18-3-7z" fill="#fff"/></svg></div>
      </div>
    </div>
  </div>
</section>

<footer class="site-footer">
  <div class="wrap">
    <div class="foot-col" style="left:4px">
      <h4>Contact Us</h4>
      <ul class="contact-list">
        <li><svg width="10" height="12" viewBox="0 0 10 12"><path d="M5 0a4.5 4.5 0 0 0-4.5 4.5C.5 8 5 12 5 12s4.5-4 4.5-7.5A4.5 4.5 0 0 0 5 0z" fill="#ee5a24"/></svg><span>48 Harbour Lane, MAPLE RIDGE,<br>Ohio, 40410.</span></li>
        <li><svg width="11" height="11" viewBox="0 0 24 24"><path d="M6.6 10.8a15 15 0 0 0 6.6 6.6l2.2-2.2a1 1 0 0 1 1-.25 11.4 11.4 0 0 0 3.6.57 1 1 0 0 1 1 1V20a1 1 0 0 1-1 1A17 17 0 0 1 3 4a1 1 0 0 1 1-1h3.5a1 1 0 0 1 1 1c0 1.25.2 2.45.57 3.57a1 1 0 0 1-.25 1z" fill="#ee5a24"/></svg><span>1800 555 01234</span></li>
        <li><svg width="12" height="10" viewBox="0 0 12 10"><rect width="12" height="10" fill="#ee5a24"/><path d="M0 0l6 5 6-5" fill="none" stroke="#333" stroke-width="1.2"/></svg><span>hello@handsethaven.example</span></li>
      </ul>
    </div>
    <div class="foot-col" style="left:361px">
      <h4>Handset Haven</h4>
      <ul><li>About Us</li><li>Market Reviews</li><li>Terms of Use</li><li>Privacy Policy</li><li>Site Map</li></ul>
    </div>
    <div class="foot-col" style="left:556px">
      <h4>Customer Service</h4>
      <ul><li>Shipping Policy</li><li>Compensation First</li><li>My Account</li><li>Return Policy</li><li>Contact Us</li></ul>
    </div>
    <div class="foot-col" style="left:848px">
      <h4>Payment &amp; Shipping</h4>
      <ul><li>Terms of Use</li><li>Payment Methods</li><li>Shipping Guide</li><li>Locations We Ship To</li><li>Estimated Delivery Time</li></ul>
    </div>
  </div>
</footer>
<div class="bottom-bar"><div class="wrap">Handset Haven Inc © 2017 . All Rights Reserved.</div></div>

</body>
</html>
```